Enlighted Feel-Good Wrapper Design for Cannabis Snack Bar: Vesko Bites.

We need a logo and wrapper for the first product in our line-up, Pip Crackle Maple! - Honey Salted Nuts and Dark Chocolate. Please highlight the name Maple Pip Crackle!, more than the name Vesko Bites or flavor of the bar. The package dimensions unfolded and unsealed are 6.5 inches x 5.25 inches. I have uploaded 3 photos of similar bar wrappers as an example of the wrapper type. The winning design will be awarded an extra amount for the Vesko Bites logo from Craft Hive.

It is a nut based snack bar similar to brands like Brisk, Stellar Munch, Orla, and Rover Bars. The difference is that this bar will contain THC and/or CBD oils. It is designed for the Medical Marijuana market in California. I would like the bar to be more upscale in design as we are going after a demographic with a higher disposable income and will be in their 30's-60's. We would like the brand to be appealing to both men and women. We would like the wrapper/logo to have an air of enlightenment to it. We want people to feel like they will be at peace when they eat this bar. Please do not make the design flashy, or decorated with marijuana leaves. We do not want something cheesy. We uploaded pictures of the bar so you can see what they look like. The packaging has to be OPAQUE.

Please include all the following. If you don't know specific values, weights or ingredients please fill the space with any text that can be substituted.

Label Regulatory Requirements:

(1) The identity of the product in a text size reasonably related to the most prominent printed matter on the panel;
(2) The words “cannabis-infused” immediately above the identity of the product in bold type and a text size larger than the text size used for the identity of the product;
(3) The cannabis product symbol uploaded in this post. The symbol shall be no smaller in size than half (.5) inch by half (.5) inch and shall be printed legibly and conspicuously;
(4) The net weight or volume of the contents of the package;

1.4 oz (40g)

(5) The THC content and CBD content for the package in its entirety, expressed in milligrams per package;

40mg

(6) The THC content and CBD content per serving, expressed in milligrams per serving;

10mg

(b) The primary panel text must be in type size no less than 6 point font and be in relation to the size of the primary panel and container.

40408. Informational Panel Labeling Requirements.
(a) The label for a medical cannabis product shall include an informational panel that includes the following:
(1) The licensed manufacturer and its contact number or website address;

Vesko Bites, San Diego, CA (555)302-7194, www.veskobites.example

(2) The date of manufacture;
(3) Each of the following statements:
(A) “SCHEDULE I CONTROLLED SUBSTANCE.”
(B) “KEEP OUT OF REACH OF CHILDREN AND ANIMALS” in bold print.
(C) “FOR MEDICAL USE ONLY.”
(D) “IF PREGNANT OR BREASTFEEDING, CONSULT A PHYSICIAN PRIOR TO USE.”
(E) “THE INTOXICATING EFFECTS OF THIS PRODUCT MAY BE DELAYED BY UP TO TWO HOURS.”
(F) “THIS PRODUCT MAY IMPAIR THE ABILITY TO DRIVE OR OPERATE MACHINERY, PLEASE USE EXTREME CAUTION.”
(4) A list of all product ingredients in descending order of predominance by weight or volume;

NUT MIXTURE:
almonds, peanuts, walnuts, puffed rice, flaxseed

SYRUP:
honey, brown rice syrup, sea salt, vanilla

CHOCOLATE DRIZZLE:
dark chocolate, coconut oil

(5) If an edible product that contains an ingredient, flavoring, coloring, or an incidental additive that bears or contains a major food allergen, the word “contains,” followed by a list of the applicable major food allergens;

Contains tree nuts.

(6) If an edible product, the names of any artificial food colorings contained in the product;
(7) If an edible product, the amount, in grams, of sodium, sugar, carbohydrates, and total fat per serving;

Dark Chocolate Sea Salt: 193 calories, 12.5g fat, 95mg sodium, 18.9g carbs, 2.1g fiber, 14g sugars, 5.2g protein

(8) The lot number;
(9) Instructions for use, such as the method of consumption or application, and any preparation necessary prior to use;
(10) The product expiration date, “use by” date, or “best by” date; and
(11) The unique identifier.
(b) The informational panel text shall be in a type size of no less than 6 point font and in relation to the size of the primary panel and container, unless there is insufficient area on the container available to print all the required information in a type size of no less than 6 point font. In such a case, the label shall include the warning statements required by paragraph (3) in a type size of no less than 6 point font, and the product shall be accompanied by a supplemental labeling that includes all of the information required by this section. The text of the supplemental labeling shall be no less than 8 point font.

The label shall not contain any of the following:

(a) Claims that the manufactured cannabis or cannabis product was grown in a California county when the cannabis was not grown there.
(b) The name of a California county unless the cannabis was grown there.
(c) Content that is or designed to be attractive to individuals under the age of 21, including but not limited to:
(1) Cartoons;
(2) Any likeness to images, characters, or phrases that are popularly used to advertise to children; or
(3) Any imitation of candy packaging or labeling.
(d) False labeling information. Labeling is false if it is false or misleading in any particular.
(e) Claims of health benefits or other physical benefits.
Updates

Industry/Entity Type

Retail

Logo Text

Vesko Bites

Colors

Designer to choose colors to be used in the design.

Requirements
Must have
• I would like to have a logo/icon of an cute owl or icon of a small tree branch with leaves and nut hanging off or anything else that you think would be a good logo incorporated with the company name "Vesko Bites." I uploaded a logo of an owl logo that I like. Feel free to adjust and create something creative, please do not copy it.
• The wrapper needs to reflect an upscale, natural, farm fresh, whole food product. We are trying to build a high end line of products that appeal to health conscious women and men ages 30 - 60 years old.
• Please include text from Allergen warning in one of the uploaded photos.
• Please add - "Gluten free" to the label, "Non GMO" or "GMO Free" and "No Soy" or "Soy Free", and "Dairy Free" as either writing or as an icon of some sort.
Nice to have
• Please see posted photos of some wrappers of food products that I like for ideas. Some color suggestions to incorporate: Red, Yellow, Green, Orange simply because these colors have been proven appealing to the eye for food labels. You may use one or a few of these and can balance them out with other colors. Please do not use traditional colors associated with cannabis such as dark brown or deep green. Subdued, natural looking versions of these may be okay if they are balanced out with other colors or the rest of the bar. I would also like the wrapper to have some graphics that can illustrate what the bar actually looks like so that people know whats inside!
• The final design should communicate:
• Freshness
• Organic
• Healthy
• Modern
Should not have
• I do not want this product to have graphics of typical cheesy cannabis/marijuana leaves or any other low class graphics related to the industry. Not graphics of marijuana flower, joints, smoke or leaves.

```html
<!DOCTYPE html>
<html lang="en">
<head>
<meta charset="utf-8">
<title>Vesko Bites – Maple Pip Crackle! wrapper</title>
<link href="https://fonts.googleapis.com/css2?family=Libre+Baskerville:wght@700&family=Open+Sans:wght@400;600;700;800&family=Roboto+Condensed:wght@300;400&display=swap" rel="stylesheet">
<style>
  :root{
    --backdrop:#ececec;
    --wrap-white:#f7f7f7;
    --wrap-shade:#dcdcdc;
    --end-red:#c81e28;
    --end-red-dark:#9e1620;
    --band-gold:#c8882f;
    --honey:#f3b724;
    --ink-brown:#4a1f14;
    --cream:#fff8ec;
  }
  *{box-sizing:border-box;margin:0;padding:0}
  html,body{width:1200px;height:1200px;overflow:hidden;background:var(--backdrop)}
  .canvas{position:relative;width:1200px;height:1200px;font-family:"Open Sans",Arial,sans-serif;color:var(--ink-brown)}
  .shapes{position:absolute;inset:0}
  .t{position:absolute;white-space:nowrap}

  .infused{left:188px;top:172px;width:156px;text-align:center;font-family:"Libre Baskerville",Georgia,serif;font-weight:700;font-size:20px;line-height:21px;color:#fff}
  .brand-name{left:180px;top:292px;font-weight:800;font-size:27px;line-height:36px;color:var(--ink-brown)}
  .flavor-title{left:400px;top:318px;font-family:"Libre Baskerville",Georgia,serif;font-weight:700;font-size:41px;letter-spacing:1px;color:var(--cream)}
  .flavor-sub{left:420px;top:372px;font-family:"Libre Baskerville",Georgia,serif;font-weight:700;font-size:22px;letter-spacing:.5px;color:var(--cream)}
  .potency{left:812px;top:278px;font-family:"Roboto Condensed",Arial,sans-serif;font-weight:300;font-size:13px;line-height:16px;color:var(--ink-brown)}
  .bar-tag{left:940px;top:339px;font-family:"Libre Baskerville",Georgia,serif;font-weight:700;font-size:17px;letter-spacing:2px;color:#fff}
  .claims{left:898px;top:384px;width:124px;text-align:center;font-family:"Libre Baskerville",Georgia,serif;font-weight:700;font-size:13.5px;line-height:15px;color:var(--ink-brown)}
  .net-weight{left:184px;top:422px;font-size:26px;color:var(--ink-brown)}
  .thc-mark{font-family:"Libre Baskerville",Georgia,serif;font-weight:700;fill:#fff;text-anchor:middle}

  .maker{left:213px;top:612px;font-size:12px;line-height:17px;color:var(--ink-brown)}
  .maker b{font-weight:700}
  .lot{left:887px;top:614px;font-size:9.5px;line-height:12px;font-weight:700}
  .warnings{left:213px;top:760px;font-family:"Roboto Condensed",Arial,sans-serif;font-size:11px;line-height:13.5px}
  .nutrition{left:213px;top:825px;font-family:"Roboto Condensed",Arial,sans-serif;font-size:8.8px}
  .ingredients{left:676px;top:758px;font-size:10.5px;line-height:14px}
  .ingredients b{font-weight:700;font-size:9px}
  .ingredients .allergen{font-weight:700;font-size:10.5px}
</style>
</head>
<body>
<div class="canvas">
  <svg class="shapes" width="1200" height="1200" viewBox="0 0 1200 1200">
    <defs>
      <linearGradient id="photoBar" x1="0" x2="1">
        <stop offset="0" stop-color="#e9d49a"/><stop offset=".4" stop-color="#8a4a2a"/><stop offset=".7" stop-color="#d8b572"/><stop offset="1" stop-color="#6b3620"/>
      </linearGradient>
      <linearGradient id="nuts" x1="0" x2="1">
        <stop offset="0" stop-color="#c8785a"/><stop offset=".5" stop-color="#e8c77e"/><stop offset="1" stop-color="#9a5a38"/>
      </linearGradient>
    </defs>

    <g class="front-panel">
      <path d="M90 122 L1102 122 L1102 492 L90 492 Z" fill="var(--wrap-white)"/>
      <rect x="90" y="122" width="68" height="370" fill="var(--end-red)"/>
      <rect x="100" y="122" width="3" height="370" fill="var(--end-red-dark)"/>
      <rect x="115" y="122" width="3" height="370" fill="var(--end-red-dark)"/>
      <rect x="1044" y="122" width="58" height="370" fill="var(--wrap-shade)" opacity=".5"/>
      <rect role="img" aria-label="Photo of the bar: nuts and puffed rice bound in honey with dark chocolate drizzle" x="176" y="170" width="820" height="110" rx="40" fill="url(#photoBar)"/>
      <path d="M160 272 Q420 262 700 272 T1060 270 L1060 468 Q600 458 160 474 Z" fill="var(--band-gold)"/>
      <path d="M168 166 L358 166 L236 286 Z" fill="var(--end-red)"/>
      <path d="M948 230 L1038 230 L993 305 Z" fill="var(--end-red)" stroke="#3aa0d8" stroke-width="3"/>
      <text class="thc-mark" x="993" y="256" font-size="17">THC</text>
      <text class="thc-mark" x="993" y="278" font-size="17">!</text>
      <rect x="926" y="334" width="86" height="30" rx="15" fill="var(--honey)"/>
    </g>

    <g class="back-panel">
      <rect x="92" y="548" width="1012" height="370" fill="var(--wrap-white)"/>
      <rect x="92" y="548" width="48" height="370" fill="var(--wrap-shade)" opacity=".5"/>
      <rect x="1036" y="548" width="68" height="370" fill="var(--end-red)"/>
      <rect x="1084" y="548" width="3" height="370" fill="var(--end-red-dark)"/>
      <rect x="1070" y="548" width="3" height="370" fill="var(--end-red-dark)"/>
      <rect x="92" y="714" width="944" height="36" fill="#ffffff"/>
      <rect x="92" y="722" width="944" height="2" fill="var(--wrap-shade)"/>
      <rect x="92" y="740" width="944" height="2" fill="var(--wrap-shade)"/>
      <path d="M468 636 L556 636 L510 708 Z" fill="var(--end-red)" stroke="#3aa0d8" stroke-width="3"/>
      <text class="thc-mark" x="511" y="661" font-size="17">THC</text>
      <text class="thc-mark" x="511" y="682" font-size="17">!</text>
      <path role="img" aria-label="Scattered almonds, peanuts, walnuts and macadamia nuts" d="M560 690 Q560 668 590 668 L740 650 L776 600 Q800 592 836 600 Q852 612 840 640 L790 676 L730 716 L620 738 Q566 742 560 712 Z" fill="url(#nuts)" opacity=".75"/>
    </g>
  </svg>

  <div class="t infused">CANNABIS<br>INFUSED</div>
  <div class="t brand-name">VESKO BITES</div>
  <div class="t flavor-title">MAPLE PIP CRACKLE!</div>
  <div class="t flavor-sub">SALTED DARK CHOCOLATE &amp; NUTS</div>
  <div class="t potency">THC content 40mg/pack<br>CBD content 10mg/serving</div>
  <div class="t bar-tag">BAR</div>
  <div class="t claims">NON-GMO<br>GLUTEN-FREE<br>NO SOY<br>DAIRY-FREE</div>
  <div class="t net-weight">40g</div>

  <div class="t maker">Vesko Bites, San Diego, CA (555)302-7194, www.veskobites.example<br>08/09/2017<br>SCHEDULE I CONTROLLED SUBSTANCE.<br><b>KEEP OUT OF REACH OF CHILDREN</b><br><b>AND ANIMALS.</b> FOR MEDICAL USE ONLY.</div>
  <div class="t lot">LOT NO. 16776<br>USE BY: 11/05/2018</div>
  <div class="t warnings">IF PREGNANT OR BREASTFEEDING, CONSULT A PHYSICIAN PRIOR TO USE.<br>THE INTOXICATING EFFECTS OF THIS PRODUCT MAY BE DELAYED BY UP TO TWO HOURS.<br>THIS PRODUCT MAY IMPAIR THE ABILITY TO DRIVE OR OPERATE MACHINERY,<br>PLEASE USE EXTREME CAUTION.</div>
  <div class="t nutrition">Dark Chocolate Sea Salt: 193 calories, 12.5g fat, 95mg sodium, 18.9g carbs, 2.1g fiber, 14g sugars, 5.2g protein</div>
  <div class="t ingredients">INGREDIENTS:<br><b>NUT MIXTURE:</b> almonds, peanuts, walnuts, puffed rice, flaxseed<br><b>SYRUP:</b> honey, brown rice syrup, sea salt, vanilla<br><b>CHOCOLATE DRIZZLE:</b> dark chocolate, coconut oil<br><span class="allergen">Contains tree nuts.</span></div>
</div>
</body>
</html>
```